Create a memorable Web Design for real estate branding

we are a Minnepolis brokerage and boutique housing specialist with over 27 years of experience in the Global furnished housing industry, servicing the Greater Los Angeles area. Specializing in “warm environments” we offer a customized approach to satisfying our guests and client’s needs by offering a wide array of options in highly desirable areas. Additionally, Lantern Dwelling Partners offers assistance and expertise to home buyers, sellers and investors.

Industry/Entity Type

Real Estate

Number of Pages Required

1 page

Font styles to use
Serif
Sans Serif
Decorative

```html
<!DOCTYPE html>
<html lang="en">
<head>
<meta charset="utf-8">
<title>Lantern Dwelling Partners — Real Estate</title>
<link href="https://fonts.googleapis.com/css2?family=Raleway:ital,wght@0,400;0,500;0,600;0,700;0,800;1,400&display=swap" rel="stylesheet">
<style>
:root{
  --teal:#1a9a7e;
  --teal-dark:#14836b;
  --green:#8cc63f;
  --ink:#2b2b2b;
  --text:#555;
  --muted:#8a8a8a;
  --light:#f2f2f2;
  --white:#fff;
  --footer:#2f2f2f;
  --footer-bottom:#242424;
}
*{box-sizing:border-box;margin:0;padding:0}
html,body{width:1200px;height:3141px;overflow:hidden}
body{font-family:"Raleway",Arial,sans-serif;color:var(--text);background:var(--white);position:relative}
.abs{position:absolute}
.btn{position:absolute;display:flex;align-items:center;justify-content:center;color:var(--white);font-weight:700;text-transform:uppercase;font-size:15px;letter-spacing:.3px}
.btn-teal{background:var(--teal)}
.btn-green{background:var(--green)}

/* header */
.topline{top:0;left:0;width:1200px;height:5px;background:var(--green)}
.header{top:5px;left:0;width:1200px;height:106px;background:var(--white)}
.brand{top:22px;left:75px;color:var(--teal);font-weight:700;font-size:34px;line-height:1.05}
.brand small{display:block;font-size:20px;font-weight:700;letter-spacing:1px}
.header-phone{top:38px;left:893px;display:flex;align-items:center;gap:10px;color:var(--teal);font-size:19px;font-weight:500}
.header-search{top:39px;left:1106px}
.nav{top:111px;left:0;width:1200px;height:57px;background:linear-gradient(180deg,#22b08f,var(--teal));display:flex;align-items:center;padding-left:75px;gap:0}
.nav a{color:var(--white);text-decoration:none;font-size:13.5px;font-weight:700;text-transform:uppercase;margin-right:43px}

/* hero */
.hero{top:168px;left:0;width:1200px;height:550px;background:linear-gradient(180deg,#5f86b8 0%,#9db6d2 30%,#7f8f86 55%,#56663f 78%,#3a4630 100%)}
.hero-title{top:320px;left:0;width:1200px;text-align:center;color:var(--white);font-weight:800;font-size:60px;line-height:64px;letter-spacing:1px;text-transform:uppercase;text-shadow:0 2px 6px rgba(0,0,0,.35)}
.hero-arrow{top:360px}
.search-band{top:561px;left:0;width:1200px;height:157px;background:rgba(20,20,20,.72)}
.search-title{top:593px;left:75px;color:var(--green);font-weight:700;font-size:25px;text-transform:uppercase}
.field{position:absolute;top:641px;height:42px;background:var(--white);font-size:14px;color:#555;display:flex;align-items:center;padding-left:12px}
.field.select::after{content:"";position:absolute;right:14px;top:17px;width:6px;height:6px;border-right:1.5px solid #666;border-bottom:1.5px solid #666;transform:rotate(45deg)}

/* featured */
.section-title{position:absolute;left:0;width:1200px;text-align:center;color:var(--ink);font-weight:700;font-size:24px;text-transform:uppercase;letter-spacing:.5px}
.card{position:absolute;top:900px;width:331px;height:380px;background:var(--light)}
.card-photo{width:331px;height:233px}
.card-head{position:absolute;top:250px;left:20px;color:var(--teal);font-weight:700;font-size:16px;text-transform:uppercase}
.card-sub{position:absolute;top:274px;left:20px;font-size:16px;color:#555}
.card-price{position:absolute;top:320px;left:20px;font-weight:700;font-size:19px;color:var(--ink)}
.card .btn{top:312px;left:136px;width:120px;height:42px;font-size:14px;text-transform:none}

/* services band */
.services{top:1441px;left:0;width:1200px;height:402px;background:linear-gradient(90deg,#2e2b28,#4a4642 45%,#3a3733 100%)}
.service{position:absolute;top:1494px;width:360px;text-align:center}
.service .icon{width:120px;height:120px;margin:0 auto;border-radius:50%;background:var(--green);display:flex;align-items:center;justify-content:center}
.service h3{margin-top:38px;color:var(--green);font-size:22px;font-weight:700;text-transform:uppercase}
.service p{margin:12px auto 0;width:300px;color:#cfcfcf;font-size:15px;line-height:26px}

/* news */
.news{position:absolute;top:1960px;width:500px}
.date{position:absolute;top:0;left:0;width:80px}
.date .m{height:38px;background:var(--green);color:var(--white);font-size:13px;font-weight:700;display:flex;align-items:center;justify-content:center}
.date .d{height:46px;background:var(--ink);color:var(--white);font-size:28px;font-weight:700;display:flex;align-items:center;justify-content:center}
.news h4{position:absolute;top:-4px;left:97px;color:var(--teal);font-size:23px;font-weight:700;white-space:nowrap}
.news p{position:absolute;top:30px;left:97px;width:410px;font-size:14.5px;line-height:24.5px;color:#555}
.news .btn{top:148px;left:97px;width:124px;height:42px;font-size:14px}

/* testimonials */
.testi-photo{top:2307px;left:0;width:496px;height:323px;background:linear-gradient(135deg,#a9b9c6 0%,#d9c7a4 45%,#e7d8bf 60%,#7f8f5a 100%)}
.testi-panel{top:2307px;left:496px;width:704px;height:323px;background:#efefef}
.testi-title{top:2358px;left:546px;color:var(--ink);font-weight:700;font-size:26px;text-transform:uppercase}
.testi-quote{top:2410px;left:546px;width:585px;font-style:italic;font-size:15px;line-height:26px;color:#555}
.testi-name{top:2500px;left:546px;color:var(--teal);font-weight:600;font-size:19px}
.testi-nav{top:2563px;left:550px;display:flex;gap:8px}

/* newsletter */
.input{position:absolute;top:2724px;height:42px;background:#ececec;font-size:14px;color:#666;display:flex;align-items:center;padding-left:16px}

/* footer */
.footer{top:2881px;left:0;width:1200px;height:199px;background:var(--footer)}
.footer-brand{top:2918px;left:75px;color:var(--green);font-weight:700;font-size:26px;line-height:1.05}
.footer-brand small{display:block;font-size:16px;letter-spacing:1px}
.footer-about{top:2984px;left:75px;width:320px;font-size:13.5px;line-height:25px;color:#bdbdbd}
.footer-h{position:absolute;top:2914px;color:var(--green);font-size:13.5px;font-weight:700;text-transform:uppercase}
.footer-list{position:absolute;top:2940px;list-style:none;font-size:13px;line-height:26px;color:#d5d5d5}
.contact{top:2940px;left:705px;font-size:13px;line-height:22px;color:#d5d5d5;width:200px}
.contact strong{color:var(--white)}
.contact .row{display:flex;align-items:center;gap:10px;margin-top:6px}
.socials{top:2943px;left:942px;display:flex;gap:6px}
.socials span{width:30px;height:30px;border-radius:50%;background:var(--white);display:block}
.footer-bottom{top:3080px;left:0;width:1200px;height:61px;background:var(--footer-bottom);color:#9a9a9a;font-size:12.5px;display:flex;align-items:center;justify-content:center}
</style>
</head>
<body>

<div class="abs topline"></div>
<header class="abs header">
  <div class="abs brand">Lantern Dwelling<small>Real Estate</small></div>
  <div class="abs header-phone">
    <svg width="16" height="16" viewBox="0 0 24 24"><path fill="#1a9a7e" d="M6.6 10.8a15.1 15.1 0 0 0 6.6 6.6l2.2-2.2c.3-.3.7-.4 1-.2 1.1.4 2.3.6 3.6.6.6 0 1 .4 1 1V20c0 .6-.4 1-1 1A17 17 0 0 1 3 4c0-.6.4-1 1-1h3.5c.6 0 1 .4 1 1 0 1.3.2 2.5.6 3.6.1.3 0 .7-.2 1z"/></svg>
    1-800-555-0142
  </div>
  <svg class="abs header-search" width="20" height="20" viewBox="0 0 24 24"><circle cx="10" cy="10" r="6.5" fill="none" stroke="#222" stroke-width="2.6"/><path d="M15 15l6 6" stroke="#222" stroke-width="2.8" stroke-linecap="round"/></svg>
</header>

<nav class="abs nav">
  <a>Home</a><a>About Us</a><a>Services</a><a>Property</a><a>Blog</a><a>Testimonials</a><a>Latest News</a><a>Careers</a><a>Contact Us</a>
</nav>

<section class="abs hero" role="img" aria-label="Photo of a large two-storey family house with trees under a blue sky"></section>
<h1 class="abs hero-title">Specializing in<br>warm environments</h1>
<svg class="abs hero-arrow" style="left:60px" width="24" height="44" viewBox="0 0 24 44"><path d="M20 4L4 22l16 18" fill="none" stroke="#fff" stroke-width="3"/></svg>
<svg class="abs hero-arrow" style="left:1116px" width="24" height="44" viewBox="0 0 24 44"><path d="M4 4l16 18L4 40" fill="none" stroke="#fff" stroke-width="3"/></svg>

<div class="abs search-band"></div>
<h2 class="abs search-title">Search Property</h2>
<div class="field" style="left:75px;width:319px">Enter Location</div>
<div class="field" style="left:401px;width:138px">Max Price</div>
<div class="field" style="left:545px;width:136px">Min Price</div>
<div class="field select" style="left:689px;width:138px">Bedroom</div>
<div class="field select" style="left:833px;width:138px">Bathroom</div>
<div class="btn btn-green" style="top:641px;left:989px;width:137px;height:42px;font-size:16px">Search</div>

<h2 class="section-title" style="top:846px">Featured Property</h2>

<article class="card" style="left:75px">
  <div class="card-photo" role="img" aria-label="Photo of a modern house lit at dusk beside a pool" style="background:linear-gradient(180deg,#3a4f7a,#6a6a7a 55%,#3f8ba5 85%,#2a3a4a)"></div>
  <div class="card-head">Property Heading</div>
  <div class="card-sub">Birchwood Towers (NY, 280m2)</div>
  <div class="card-price">$ 510,000</div>
  <div class="btn btn-green">More Info</div>
</article>
<article class="card" style="left:433px">
  <div class="card-photo" role="img" aria-label="Photo of a two-storey suburban house with a green lawn" style="background:linear-gradient(180deg,#5c8fd1,#c9b594 50%,#6f8a45 85%,#4a6a2a)"></div>
  <div class="card-head">Property Heading</div>
  <div class="card-sub">Birchwood Towers (NY, 280m2)</div>
  <div class="card-price">$ 510,000</div>
  <div class="btn btn-green">More Info</div>
</article>
<article class="card" style="left:794px">
  <div class="card-photo" role="img" aria-label="Photo of a grey stone family house with a double garage" style="background:linear-gradient(180deg,#dfe6ee,#9a9a98 45%,#7c8a6a 85%,#5f7a3f)"></div>
  <div class="card-head">Property Heading</div>
  <div class="card-sub">Birchwood Towers (NY, 280m2)</div>
  <div class="card-price">$ 510,000</div>
  <div class="btn btn-green">More Info</div>
</article>

<div class="btn btn-teal" style="top:1334px;left:471px;width:258px;height:52px">View All Property</div>

<section class="abs services" role="img" aria-label="Dimmed photo of a smiling couple in front of a house"></section>
<div class="service" style="left:60px">
  <div class="icon"><svg width="50" height="50" viewBox="0 0 24 24"><circle cx="12" cy="7.5" r="4" fill="#fff"/><path d="M4 21c0-4.5 3.6-7 8-7s8 2.5 8 7z" fill="#fff"/></svg></div>
  <h3>About Us</h3>
  <p>Aliquam molestie, mi et imperdiet euismod, dui purus auctor tellus, et interdum lacus lectus et ante orci luctus et ultrices posuere cubilia.</p>
</div>
<div class="service" style="left:420px">
  <div class="icon"><svg width="56" height="56" viewBox="0 0 24 24"><path d="M5 10l7-6 7 6v5H5z" fill="none" stroke="#fff" stroke-width="1.6" stroke-linejoin="round"/><rect x="10.5" y="11" width="3" height="4" fill="#fff"/><path d="M3 19c3-2 6-2 9-1l5-1.5c1-.3 1.8.8.8 1.5L13 21H3z" fill="#fff"/></svg></div>
  <h3>Real Estate Services</h3>
  <p>Aliquam molestie, mi et imperdiet euismod, dui purus auctor tellus, et interdum lacus lectus et ante orci luctus et ultrices posuere cubilia.</p>
</div>
<div class="service" style="left:780px">
  <div class="icon"><svg width="56" height="56" viewBox="0 0 24 24"><path d="M3 11l9-8 9 8" fill="none" stroke="#fff" stroke-width="1.8" stroke-linejoin="round"/><rect x="6" y="10" width="12" height="11" fill="none" stroke="#fff" stroke-width="1.8"/><text x="12" y="19" text-anchor="middle" font-family="Raleway,sans-serif" font-weight="700" font-size="8" fill="#fff">$</text></svg></div>
  <h3>Housing Brokerage</h3>
  <p>Aliquam molestie, mi et imperdiet euismod, dui purus auctor tellus, et interdum lacus lectus et ante orci luctus et ultrices posuere cubilia.</p>
</div>

<h2 class="section-title" style="top:1888px">Whats New</h2>

<article class="news" style="left:75px">
  <div class="date"><div class="m">JUN</div><div class="d">06</div></div>
  <h4>Lorem ipsum dolor sit amet</h4>
  <p>Duis aliquam nibh a dui iaculis viverra id a velit. Vivamus egestas risus in magna varius commodo. Sed semper viverra egestas. Etiam pretium porttitor lectus, vel ornare neque porta volutpat.</p>
  <div class="btn btn-green">Read More</div>
</article>
<article class="news" style="left:614px">
  <div class="date"><div class="m">JUN</div><div class="d">06</div></div>
  <h4>Lorem ipsum dolor sit amet</h4>
  <p>Duis aliquam nibh a dui iaculis viverra id a velit. Vivamus egestas risus in magna varius commodo. Sed semper viverra egestas. Etiam pretium porttitor lectus, vel ornare neque porta volutpat.</p>
  <div class="btn btn-green">Read More</div>
</article>

<div class="btn btn-teal" style="top:2205px;left:471px;width:258px;height:52px">Read All News</div>

<div class="abs testi-photo" role="img" aria-label="Photo of a happy couple embracing in front of their home"></div>
<div class="abs testi-panel"></div>
<h2 class="abs testi-title">Testimonials</h2>
<p class="abs testi-quote">“ Duis aliquam nibh a dui iaculis viverra id a velit. Vivamus egestas risus in magna varius commodo. Sed semper viverra egestas. Etiam pretium porttitor lectus, vel omare neque porta volutpat..”</p>
<div class="abs testi-name">-Dana Holt</div>
<div class="abs testi-nav">
  <svg width="16" height="16" viewBox="0 0 16 16"><circle cx="8" cy="8" r="7" fill="none" stroke="#999" stroke-width="1.4"/><path d="M9.5 5L6.5 8l3 3" fill="none" stroke="#999" stroke-width="1.4"/></svg>
  <svg width="16" height="16" viewBox="0 0 16 16"><circle cx="8" cy="8" r="7" fill="none" stroke="#8cc63f" stroke-width="1.6"/><path d="M6.5 5l3 3-3 3" fill="none" stroke="#8cc63f" stroke-width="1.6"/></svg>
</div>

<h2 class="section-title" style="top:2672px">Newletter Sign Up</h2>
<div class="input" style="left:253px;width:333px">Enter Name</div>
<div class="input" style="left:613px;width:333px">Enter Email Address</div>
<div class="btn btn-teal" style="top:2791px;left:471px;width:258px;height:53px">Sign Up Now</div>

<footer class="abs footer"></footer>
<div class="abs footer-brand">Lantern Dwelling<small>Real Estate</small></div>
<p class="abs footer-about">Suspendisse lobortis turpis in odio blandit ac interdum lorem euismod. Etiam risus massa, vulputate eu pellentesque et.</p>

<div class="footer-h" style="left:440px">Quick Links</div>
<ul class="footer-list" style="left:440px"><li>Home</li><li>About Us</li><li>Services</li><li>Property</li><li>Blog</li></ul>
<ul class="footer-list" style="left:540px"><li>Testimonials</li><li>Latest News</li><li>Careers</li><li>Contact Us</li></ul>

<div class="footer-h" style="left:705px">Contact Us</div>
<div class="abs contact">
  <strong>Company Name</strong><br>412 Alder Lane<br>Minneapolis, MN 55401
  <div class="row"><svg width="12" height="12" viewBox="0 0 24 24"><path fill="#ddd" d="M6.6 10.8a15.1 15.1 0 0 0 6.6 6.6l2.2-2.2c.3-.3.7-.4 1-.2 1.1.4 2.3.6 3.6.6.6 0 1 .4 1 1V20c0 .6-.4 1-1 1A17 17 0 0 1 3 4c0-.6.4-1 1-1h3.5c.6 0 1 .4 1 1 0 1.3.2 2.5.6 3.6.1.3 0 .7-.2 1z"/></svg>1-800-555-0142</div>
  <div class="row" style="margin-top:2px"><svg width="12" height="10" viewBox="0 0 24 18"><rect width="24" height="18" rx="2" fill="#ddd"/><path d="M1 2l11 8 11-8" fill="none" stroke="#2f2f2f" stroke-width="2"/></svg>hello@lanterndwelling.com</div>
</div>

<div class="footer-h" style="left:942px">Connect Us</div>
<div class="abs socials"><span></span><span></span><span></span><span></span><span></span></div>

<div class="abs footer-bottom">Copyright © 2016. Company Name All Right Reserved</div>

</body>
</html>
```